Wheelo Ridex Car Co-Hosting program

I want to create an ad on Pictorell, graphic design with my company name is Wheelo Ridex . I am a host on the Vanta platform and I rent my cars out.
I have 90+ cars..
I’m trying to reach people that Have an extra car laying around or just tired of their car but are stuck with the payments.
And tell them Unlock earning potential with your car!
List it on our fleet for hassle-free renting on Vanta.
We manage A-Z and you profit.
Start now!
Dm us year, make, model and current mileage on odometer to find out if you qualify!
Vehicle must have a clean title and must be registered to you!

Target Market(s)

People that have an extra car laying around or are tired of their car and warm to get into a new car but they are stuck with the payments of their original car. We can take their car and rent it out for them.

Industry/Entity Type

Car rental fleet management

Requirements
Must have
• Car rental, money, profit, etc

```html
<!DOCTYPE html>
<html lang="en">
<head>
<meta charset="utf-8">
<title>Wheelo Ridex – Car Co-Hosting on Vanta</title>
<link rel="stylesheet" href="https://fonts.googleapis.com/css2?family=Montserrat:ital,wght@1,300;1,400;1,500&display=swap">
<style>
  :root {
    --ink-black: #000000;
    --night: #141314;
    --charcoal: #2b2a2d;
    --crimson: #8e1f24;
    --crimson-deep: #4a1115;
    --paper: #ffffff;
    --silver: #c9cbcf;
    --steel-blue: #2f8fd8;
    --gloss-black: #1d1e22;
  }
  * { margin: 0; padding: 0; box-sizing: border-box; }
  html, body {
    width: 1200px; height: 1200px; overflow: hidden;
    background: var(--paper);
  }
  .ad {
    position: relative; width: 1200px; height: 1200px; overflow: hidden;
    background: var(--paper);
    font-family: "Montserrat", "Century Gothic", sans-serif;
    font-style: italic;
  }
  .hero-photo {
    position: absolute; left: 0; top: 0; width: 1200px; height: 815px;
    background:
      radial-gradient(ellipse 420px 360px at 560px 260px, rgba(142,31,36,0.85), rgba(74,17,21,0.5) 60%, transparent 80%),
      linear-gradient(115deg, var(--night) 0%, var(--charcoal) 55%, #3a3a3d 100%);
  }
  .headline {
    position: absolute; left: 88px; top: 130px;
    color: var(--paper); font-weight: 500; font-size: 52px;
    line-height: 59px; letter-spacing: -0.5px;
  }
  .subhead {
    position: absolute; left: 88px; top: 270px;
    color: var(--paper); font-weight: 300; font-size: 40px;
    line-height: 45px; letter-spacing: -0.5px;
  }
  .promise-disc {
    position: absolute; left: 752px; top: 270px;
    width: 534px; height: 534px; border-radius: 50%;
    background: var(--paper);
  }
  .promise {
    position: absolute; left: 850px; top: 355px; width: 300px;
    text-align: center; color: var(--ink-black);
    font-weight: 500; font-size: 38px; line-height: 43px; letter-spacing: -0.5px;
  }
  .fleet-photo {
    position: absolute; left: 108px; top: 492px; width: 1092px; height: 378px;
    border-radius: 180px 40px 0 120px;
    background: linear-gradient(90deg,
      var(--steel-blue) 0%, #5aaee8 14%,
      var(--gloss-black) 26%, #3a3c42 48%, var(--gloss-black) 62%,
      var(--silver) 74%, #e4e5e8 88%, #b7b9bd 100%);
  }
  .cta-band {
    position: absolute; left: 0; top: 814px; width: 1200px; height: 150px;
    background: var(--ink-black);
  }
  .torn-edge { position: absolute; left: 0; top: 948px; width: 1200px; height: 34px; }
  .cta {
    position: absolute; left: 0; top: 862px; width: 1186px;
    text-align: center; color: var(--paper);
    font-weight: 300; font-size: 66px; line-height: 76px; letter-spacing: -1px;
  }
  .qualify {
    position: absolute; left: 200px; top: 1008px; width: 786px;
    text-align: center; color: var(--ink-black);
    font-weight: 300; font-size: 34px; line-height: 38px; letter-spacing: -0.5px;
  }
</style>
</head>
<body>
  <main class="ad">
    <div class="hero-photo" role="img" aria-label="Close-up of a red car's front headlight against a dark background"></div>

    <h1 class="headline">Unlock Earning Potential<br>With Your Car!</h1>
    <p class="subhead">List it on our fleet for<br>hassle-free renting<br>on Vanta.</p>

    <div class="promise-disc"></div>
    <p class="promise">We manage<br>A-Z and you<br>profit!</p>

    <div class="cta-band"></div>
    <div class="fleet-photo" role="img" aria-label="Lineup of three cars: a blue hatchback, a black sedan and a silver sedan"></div>

    <svg class="torn-edge" viewBox="0 0 1200 34" preserveAspectRatio="none" aria-hidden="true">
      <path fill="#000000" d="M0 0 H1200 V14 L1170 12 L1140 18 L1100 13 L1060 16 L1010 12 L960 17 L900 13 L860 19 L820 14 L770 17 L720 12 L690 18 L640 14 L600 20 L560 15 L520 18 L470 13 L430 19 L380 15 L340 18 L300 13 L250 17 L200 14 L160 20 L120 15 L80 18 L40 14 L20 22 L0 30 Z"/>
    </svg>

    <p class="cta">START NOW!</p>

    <p class="qualify">Dm us year, make, model and current<br>mileage on odometer to find out if<br>you qualify!</p>
  </main>
</body>
</html>
```